Dynamic Business Card for Sports Supplements Company

Hi! I'm looking for an awesome business card to match my existing sports supplement company. I have uploaded my current company logo and screenshot of the front page of my website.

I would like to have something dynamic and interesting and utilize the colors in the website - the reds and purples

The business card should be double sided and focus on a unique eye-catching design on the back and include all the relevant company info.

Most importantly, it should say somewhere: "Sign up on our website for a coupon code."

Target Market(s)

Mostly for women gym goers but it shouldn't be too feminine. It should be in keeping with the website design. It should flow and clearly be connected to it

Industry/Entity Type

Business

Contact Information for Business Card

Lorraine K. Vestal
CEO
LVestal@Quorvanexco.com
www.quorvanexco.com
555.417.3820
P.O. Box 47315
Burke, Virginia 00000

Sign up on our website for a coupon code

Font styles to use
Serif
Sans Serif
Other font styles liked:
• Novecento font family and "Quorvanex" is in AR Destine font

Requirements
Must have
• One side should be a bold Quorvanex logo design. Even just the symbol itself may be o.k. (see attached file)

```html
<!DOCTYPE html>
<html lang="en">
<head>
<meta charset="utf-8">
<title>Quorvanex Business Card</title>
<link rel="stylesheet" href="https://fonts.googleapis.com/css2?family=Arimo:wght@400;700&display=swap">
<style>
  :root {
    --backdrop: #5a4a3c;
    --card-black: #000000;
    --brand-red: #ed1c24;
    --ink-white: #ffffff;
    --tagline-grey: #9a9a9a;
  }
  html, body {
    margin: 0;
    padding: 0;
    width: 1200px;
    height: 987px;
    overflow: hidden;
    background: var(--backdrop);
    font-family: "Arimo", Arial, sans-serif;
  }
  .canvas {
    position: relative;
    width: 1200px;
    height: 987px;
  }
  .card {
    position: absolute;
    left: 293px;
    width: 615px;
    height: 352px;
    background: var(--card-black);
    box-shadow: 0 2px 6px rgba(0,0,0,0.45);
    overflow: hidden;
  }
  .card--front { top: 130px; }
  .card--back { top: 505px; }
  .card__split {
    position: absolute;
    inset: 0;
    width: 615px;
    height: 352px;
  }
  .contact {
    position: absolute;
    left: 26px;
    top: 0;
    color: var(--ink-white);
  }
  .contact__name {
    position: absolute;
    top: 38px;
    left: 0;
    margin: 0;
    font-size: 21px;
    font-weight: 700;
    white-space: nowrap;
  }
  .contact__title {
    position: absolute;
    top: 66px;
    left: 3px;
    margin: 0;
    font-size: 16px;
    white-space: nowrap;
  }
  .contact__line {
    position: absolute;
    left: 0;
    margin: 0;
    font-size: 15px;
    white-space: nowrap;
    display: flex;
    align-items: center;
    gap: 7px;
  }
  .contact__icon { width: 14px; height: 14px; flex: none; }
  .wordmark {
    position: absolute;
    text-align: center;
    color: var(--ink-white);
  }
  .wordmark__name {
    margin: 0;
    font-weight: 700;
    text-transform: uppercase;
    line-height: 1;
    letter-spacing: 1px;
  }
  .wordmark__tagline {
    margin: 4px 0 0;
    color: var(--tagline-grey);
    text-transform: uppercase;
    letter-spacing: 1.5px;
    line-height: 1;
  }
  .card--front .wordmark { left: 278px; width: 340px; top: 204px; }
  .card--front .wordmark__name { font-size: 31px; }
  .card--front .wordmark__tagline { font-size: 11px; }
  .card--back .wordmark { left: 0; width: 615px; top: 212px; }
  .card--back .wordmark__name { font-size: 33px; }
  .card--back .wordmark__tagline { font-size: 11px; }
  .coupon-note {
    position: absolute;
    left: 0;
    width: 615px;
    top: 290px;
    margin: 0;
    text-align: center;
    color: var(--ink-white);
    font-size: 15px;
  }
</style>
</head>
<body>
<main class="canvas">
  <section class="card card--front" aria-label="Front of business card">
    <svg class="card__split" viewBox="0 0 615 352" aria-hidden="true">
      <polygon points="0,0 322,0 208,169 340,352 0,352" fill="var(--brand-red)"/>
      <polyline points="322,0 208,169 340,352" fill="none" stroke="var(--ink-white)" stroke-width="4"/>
    </svg>
    <div class="contact">
      <p class="contact__name">Lorraine K. Vestal</p>
      <p class="contact__title">CEO</p>
      <p class="contact__line" style="top:204px">P.O. Box 47315</p>
      <p class="contact__line" style="top:224px">Alder Falls, Oregon 00000</p>
      <p class="contact__line" style="top:253px">
        <svg class="contact__icon" viewBox="0 0 14 14" aria-hidden="true"><path d="M1 5 Q7 0 13 5 L11 7 L9 5 L5 5 L3 7 Z M3 8 L11 8 L12 13 L2 13 Z" fill="var(--ink-white)"/></svg>
        555.417.3820
      </p>
      <p class="contact__line" style="top:276px">
        <svg class="contact__icon" viewBox="0 0 14 14" aria-hidden="true"><rect x="1" y="3" width="12" height="8" fill="var(--ink-white)"/><polyline points="1,3 7,8 13,3" fill="none" stroke="var(--brand-red)" stroke-width="1"/></svg>
        LVestal@Quorvanexco.com
      </p>
      <p class="contact__line" style="top:299px">
        <svg class="contact__icon" viewBox="0 0 14 14" aria-hidden="true"><circle cx="7" cy="7" r="6" fill="var(--ink-white)"/><path d="M4 4 Q6 6 5 8 Q7 9 8 12 M9 3 Q8 5 10 6" fill="none" stroke="var(--brand-red)" stroke-width="1.3"/></svg>
        www.quorvanexco.com
      </p>
    </div>
    <div class="wordmark">
      <p class="wordmark__name">Quorvanex</p>
      <p class="wordmark__tagline">Your Strength Companion</p>
    </div>
  </section>

  <section class="card card--back" aria-label="Back of business card">
    <div class="wordmark">
      <p class="wordmark__name">Quorvanex</p>
      <p class="wordmark__tagline">Your Strength Companion</p>
    </div>
    <p class="coupon-note">Sign up on our website for a coupon code</p>
  </section>
</main>
</body>
</html>
```